Website for IT Security Company in Austria with small and medium business customer base

I own a one man IT security company with a customer small to medium business customer base and need a professional looking website that contains the following information:
- Home page: About the company....
- Services: The services that I offer. It would be nice to have icons if possible (e.g Active Directory icon, digital certificate icon, ...) but this is not a must have.
- About me
- Blog: This is not a must have. It would be ok to just link it to an external blog.
- Impressum
- Contact: No form, just telephone number and e-mail address
- Anything else that you think is necessary for a professional appearance
Also I attached the company design. I do have all source files for the logo if required.

Target Market(s)

Small and medium business of all branches located in Austria

Industry/Entity Type

Cyber Security

Coding

Coded - Design and coding required

Number of Pages Required

5+ page

Font styles to use
Serif
Sans Serif
Other font styles liked:
• Bitsumishi, Bankgothic

Colors

Designer to choose only greyscale colors for use in the design.

Requirements
Must have
• The website must be a mobile-first design.
The design should not be too colorful or playful.
The logo should be used as much as possible
Navigation bar with multi drop-down menu for the services that I offer.
Example:
Services
-> Implementations
-> Implementation Service A
-> Implementation Service B
-> Security Audit
-> Audit A
-> Audit B
Maybe you could have service cards that describe the services briefly and on click redirect to the site that describes the service in detail.
End of example
Logo
contact
impressum
services that I offer
about me
about the company
Nice to have
• Icons would be nice (e.g. house for homepage, letter for contact, ...)
Also for the services I offer icons would be nice (Active Directory, digtial certificates, hacking, security auditing)
For the fonts I have only sugested Bitsumishi and Bankgothic as they are part of my logo. No sure if you feel they make sense as part of the website
Should not have
• forms.
I want to the site to be made as easy as possible (HTML5, CSS, javascript/php/.net)
I do not want a wordpress template or suchlike.

```html
<!DOCTYPE html>
<html lang="en">
<head>
<meta charset="utf-8">
<title>Basalt Guard – IT Security</title>
<link href="https://fonts.googleapis.com/css2?family=Lato:wght@400;700&family=Michroma&family=Montserrat:wght@400;500&display=swap" rel="stylesheet">
<style>
:root{
  --blue:#0a78c8;
  --blue-bright:#1aa8ec;
  --ink:#111;
  --text:#555;
  --muted:#888;
  --white:#fff;
  --footer:#1c1c1c;
}
*{box-sizing:border-box;margin:0;padding:0}
html,body{width:1200px;height:3456px;overflow:hidden}
body{font-family:"Lato",sans-serif;color:var(--text);background:var(--white);position:relative}
.display{font-family:"Michroma",sans-serif;letter-spacing:.22em;text-transform:uppercase;color:var(--ink);font-weight:400}
.btn{display:inline-block;border-radius:28px;font-family:"Lato",sans-serif;font-size:17px;text-transform:uppercase;text-decoration:none}
.btn-solid{background:linear-gradient(180deg,#1690de,#0a68b4);color:#fff;padding:15px 33px}
.btn-outline{border:2px solid var(--blue);color:var(--blue);padding:14px 31px;background:#fff}
.wordmark{font-family:"Lato",sans-serif;font-weight:700;color:#fff;display:flex;align-items:center;gap:12px;letter-spacing:.08em}
.wordmark .mark{width:26px;height:26px;background:#fff;border-radius:3px}

/* hero */
.hero{position:absolute;left:0;top:0;width:1200px;height:600px;background:linear-gradient(100deg,#061630 0%,#0b2a55 45%,#0e3a70 70%,#08244a 100%);overflow:hidden}
.hero-art{position:absolute;left:660px;top:90px;width:540px;height:510px;background:radial-gradient(circle at 45% 45%,#5fc8ff 0%,#1a78c8 25%,#0c3a72 55%,rgba(8,36,74,0) 75%)}
.site-header{position:absolute;left:111px;top:14px;width:978px;height:86px;display:flex;justify-content:space-between;align-items:flex-start}
.site-header .wordmark{font-size:22px;margin-top:24px}
.main-nav{display:flex;gap:34px;margin-top:24px;font-size:17px;font-weight:700;text-transform:uppercase}
.main-nav a{color:#fff;text-decoration:none}
.main-nav a.active{color:var(--blue-bright)}
.lang{display:flex;align-items:center;gap:7px;font-size:13px;color:#fff}
.lang .flag{width:22px;height:14px;background:linear-gradient(#c8102e,#012169);display:inline-block}
.hero-title{position:absolute;left:111px;top:272px;font-size:40px;color:#fff;letter-spacing:.18em}
.hero-lead{position:absolute;left:112px;top:333px;width:520px;color:#fff;font-size:15px;line-height:26px}
.hero .btn{position:absolute;left:112px;top:406px}
.slider-arrow{position:absolute;width:40px;height:40px;border-radius:50%;background:#fff;display:flex;align-items:center;justify-content:center}
.hero .slider-arrow.prev{left:51px;top:281px}
.hero .slider-arrow.next{left:1100px;top:281px}

.divider{position:absolute;left:587px;width:26px;display:flex;flex-direction:column;align-items:center;z-index:2}
.divider .line{flex-shrink:0;width:0;height:62px;border-left:1px dashed #666}
.divider .dot{flex-shrink:0;width:22px;height:22px;background:#111;border-radius:50%;margin-top:10px}

/* welcome */
.welcome{position:absolute;left:0;top:600px;width:1200px;height:409px;text-align:center}
.welcome h1{position:absolute;left:0;right:0;top:105px;font-size:30px}
.welcome p{position:absolute;left:160px;width:880px;top:158px;font-size:13px;line-height:28.5px;color:var(--muted)}
.welcome .btn{position:absolute;left:515px;top:286px}

/* services */
.services{position:absolute;left:0;top:1009px;width:1200px;height:521px;background:radial-gradient(ellipse at 50% 30%,#fafafa,#e6e6e6 70%,#dcdcdc)}
.services h2{position:absolute;left:0;right:0;text-align:center;top:100px;font-size:29px}
.service-card{position:absolute;width:308px;height:266px;background:#fff;text-align:center;box-shadow:0 4px 14px rgba(0,0,0,.06)}
.service-card svg{margin-top:48px}
.service-card h3{font-size:20px;font-weight:400;color:#111;text-transform:uppercase;margin-top:20px}
.service-card p{font-size:13px;line-height:23px;color:#333;margin:10px 30px 0}

/* about */
.about{position:absolute;left:0;top:1530px;width:1200px;height:463px;background:linear-gradient(90deg,#070a10,#111a26 60%,#0b1018);overflow:hidden}
.about-photo{position:absolute;left:612px;top:-120px;width:1100px;height:703px;border-radius:50%;border-left:6px solid var(--blue);background:linear-gradient(160deg,#e9e7e3,#c9c2bb 60%,#8e8781)}
.about h2{position:absolute;left:111px;top:78px;font-size:27px;color:#fff}
.about p{position:absolute;left:111px;width:450px;font-size:14.5px;line-height:28.5px;color:#fff}
.about .p1{top:130px}.about .p2{top:223px}
.about .btn{position:absolute;left:112px;top:330px}

/* blog */
.blog{position:absolute;left:0;top:1993px;width:1200px;height:711px}
.blog h2{position:absolute;left:0;right:0;text-align:center;top:113px;font-size:29px}
.blog .sub{position:absolute;left:0;right:0;text-align:center;top:157px;font-size:14px;color:var(--muted)}
.post{position:absolute;top:206px;width:308px;height:414px;background:#fff;box-shadow:0 1px 6px rgba(0,0,0,.12)}
.post .thumb{height:201px}
.post .meta{display:flex;justify-content:space-between;padding:14px 9px 0 12px;font-family:"Montserrat",sans-serif;font-size:13px;color:#555}
.post .meta .date{color:var(--blue)}
.post h3{font-size:17px;font-weight:400;color:#111;text-transform:uppercase;line-height:26px;margin:14px 8px 0}
.post p{font-size:13px;line-height:24px;color:var(--muted);margin:6px 8px 0}
.post .more{display:block;margin:4px 8px 0;font-family:"Montserrat",sans-serif;font-size:15px;color:var(--blue);text-decoration:none}

/* stories */
.stories{position:absolute;left:0;top:2704px;width:1200px;height:396px;background:linear-gradient(100deg,#52c7f2,#21b1ee 50%,#04a2e6)}
.stories h2{position:absolute;left:0;right:0;text-align:center;top:92px;font-size:29px;color:#fff;letter-spacing:.2em}
.stories .avatar{position:absolute;left:173px;top:160px;width:140px;height:140px;border-radius:50%;background:linear-gradient(160deg,#f3f3f3,#9fc6e0)}
.stories blockquote{position:absolute;left:371px;top:148px;width:656px;font-size:13.5px;line-height:28.5px;color:#fff}
.stories cite{position:absolute;left:370px;top:296px;font-style:normal;font-size:20px;color:#fff}
.stories .slider-arrow.prev{left:86px;top:212px}
.stories .slider-arrow.next{left:1075px;top:212px}

/* footer */
.site-footer{position:absolute;left:0;top:3100px;width:1200px;height:295px;background:radial-gradient(ellipse at 30% 60%,#2a2a2a,var(--footer) 60%)}
.site-footer .wordmark{position:absolute;left:113px;top:168px;font-size:30px}
.site-footer .wordmark .mark{width:34px;height:34px}
.foot-col{position:absolute;top:58px}
.foot-col h4{font-family:"Michroma",sans-serif;font-weight:400;font-size:15px;color:#fff;text-transform:uppercase;margin-bottom:12px}
.foot-col a,.foot-col li{display:block;color:#ddd;font-size:13px;line-height:25.5px;text-decoration:none;list-style:none}
.contact-list li{display:flex;gap:10px;align-items:flex-start;margin-bottom:10px;line-height:25px}
.socials{display:flex;gap:7px;margin-top:6px}
.socials span{width:34px;height:34px;border-radius:50%;border:1.5px solid #fff;display:block}
.copyright{position:absolute;left:0;top:3395px;width:1200px;height:61px;background:#111;color:#fff;font-size:13px;text-align:center;line-height:61px}
</style>
</head>
<body>

<section class="hero">
  <div class="hero-art" role="img" aria-label="Hand touching a glowing padlock surrounded by security icons"></div>
  <header class="site-header">
    <div class="wordmark"><span class="mark"></span>BASALT GUARD</div>
    <nav class="main-nav">
      <a href="#" class="active">Home</a><a href="#">Blog</a><a href="#">About Me</a><a href="#">Services</a><a href="#">Contact</a><a href="#">Imprint</a>
      <span class="lang"><span class="flag"></span>ENG ⌄</span>
    </nav>
  </header>
  <h1 class="hero-title display">Basalt Guard!</h1>
  <p class="hero-lead">Lorem ipsum dolor sit amet, consectetur adipiscing elit, sed do eiusmod tempor incididunt ut labore et dolore magna aliqua.</p>
  <a class="btn btn-solid" href="#">Get Started</a>
  <span class="slider-arrow prev"><svg width="12" height="16" viewBox="0 0 12 16"><path d="M8 2 2 8l6 6" fill="none" stroke="#333" stroke-width="1.6"/></svg></span>
  <span class="slider-arrow next"><svg width="12" height="16" viewBox="0 0 12 16"><path d="M4 2l6 6-6 6" fill="none" stroke="#333" stroke-width="1.6"/></svg></span>
</section>

<section class="welcome">
  <h1 class="display">Welcome to Basalt Guard!</h1>
  <p>Cyber security incidents are unfortunately no longer a rarity , but rather commonplace. In many cases, increasing IT security could be quite easy. I am happy to support you with my profound practice and years of experience. I pursue the approach of the best possible protection with the greatest possible productivity. To do this, I largely use the functionalities that you have with the products you have already purchased.&nbsp; This creates an optimal balance between effective protection and financial expenditure.</p>
  <a class="btn btn-outline" href="#">Learn More</a>
</section>

<div class="divider" style="top:542px"><span class="line"></span><span class="dot"></span></div>

<section class="services">
  <h2 class="display">Our Services</h2>
  <article class="service-card" style="left:111px;top:160px">
    <svg width="64" height="60" viewBox="0 0 64 60" fill="none" stroke="#0a78c8" stroke-width="2"><rect x="2" y="14" width="46" height="42"/><rect x="10" y="24" width="10" height="8"/><rect x="24" y="38" width="10" height="8"/><path d="M15 32v10h9"/><circle cx="50" cy="14" r="9"/><circle cx="50" cy="14" r="4"/></svg>
    <h3>Implementations</h3>
    <p>Enterprise PKI<br>Enterprise tiering infrastructure</p>
  </article>
  <article class="service-card" style="left:446px;top:186px">
    <svg width="64" height="60" viewBox="0 0 64 60" fill="none" stroke="#0a78c8" stroke-width="2"><path d="M30 4l16 6v12c0 10-7 16-16 20-9-4-16-10-16-20V10z"/><path d="M23 22l5 5 10-10"/><path d="M2 44h12l10 4h14l20-10M2 56h14l14 2 28-14"/></svg>
    <h3>Security Check</h3>
    <p>The purpose of the security checks is to check the vulnerability of your systems</p>
  </article>
  <article class="service-card" style="left:780px;top:160px">
    <svg width="70" height="60" viewBox="0 0 70 60" fill="none" stroke="#0a78c8" stroke-width="2"><rect x="8" y="8" width="54" height="38"/><path d="M2 50h66v4H2z"/><circle cx="35" cy="20" r="6"/><path d="M24 38c2-7 20-7 22 0"/><rect x="22" y="40" width="26" height="5"/></svg>
    <h3>Security Optimization</h3>
    <p>The purpose of security optimization is to harden your systems against attacks</p>
  </article>
</section>

<section class="about">
  <div class="about-photo" role="img" aria-label="Portrait photo of the company owner"></div>
  <h2 class="display">About Me</h2>
  <p class="p1">In my almost 20 years of experience as an IT administrator, trainer, consultant and solution architect, I have been able to work for many companies in different industries and sizes.</p>
  <p class="p2">IT security, especially in the enterprise server environment, has emerged as my greatest passion. Since then I have been supporting companies in realizing their security requirements.</p>
  <a class="btn btn-solid" href="#">Learn More</a>
</section>

<section class="blog">
  <h2 class="display">Latest Blog</h2>
  <p class="sub">Quis ipsum suspendisse ultrices gravida. Risus commodo</p>
  <article class="post" style="left:111px">
    <div class="thumb" role="img" aria-label="Glowing digital globe above a city at night" style="background:linear-gradient(160deg,#0b2e6a,#2a6fd0 50%,#0a1c40)"></div>
    <div class="meta"><span class="date">▦ 6,June 2020</span><span>◌ 0 Comments</span></div>
    <h3>Lorem ipsum dolor adipiscing elit, sed do eiusmod</h3>
    <p>Lorem ipsum dolor sit amensectetur adipiscing elit, sed do eiusmod tempor iidunt ut labore et dolore magna aliqua.</p>
    <a class="more" href="#">Read More ⟶</a>
  </article>
  <article class="post" style="left:446px">
    <div class="thumb" role="img" aria-label="Team working at screens with digital interface overlay" style="background:linear-gradient(160deg,#4a6270,#2a3d4a 55%,#6e8592)"></div>
    <div class="meta"><span class="date">▦ 6,June 2020</span><span>◌ 0 Comments</span></div>
    <h3>Lorem ipsum dolor adipiscing elit, sed do eiusmod</h3>
    <p>Lorem ipsum dolor sit amensectetur adipiscing elit, sed do eiusmod tempor iidunt ut labore et dolore magna aliqua.</p>
    <a class="more" href="#">Read More ⟶</a>
  </article>
  <article class="post" style="left:780px">
    <div class="thumb" role="img" aria-label="Hands on laptops and tablets with padlock symbols overlay" style="background:linear-gradient(160deg,#6f8aa8,#30496a 55%,#8aa3bd)"></div>
    <div class="meta"><span class="date">▦ 6,June 2020</span><span>◌ 0 Comments</span></div>
    <h3>Lorem ipsum dolor adipiscing elit, sed do eiusmod</h3>
    <p>Lorem ipsum dolor sit amensectetur adipiscing elit, sed do eiusmod tempor iidunt ut labore et dolore magna aliqua.</p>
    <a class="more" href="#">Read More ⟶</a>
  </article>
</section>

<div class="divider" style="top:1930px"><span class="line"></span><span class="dot"></span></div>

<section class="stories">
  <h2 class="display">Customer Stories</h2>
  <span class="slider-arrow prev"><svg width="12" height="16" viewBox="0 0 12 16"><path d="M8 2 2 8l6 6" fill="none" stroke="#333" stroke-width="1.6"/></svg></span>
  <div class="avatar" role="img" aria-label="Customer portrait photo"></div>
  <blockquote>Lorem ipsum dolor sit amet, consectetur adipiscing elit, sed do eiusmod tempor incididunt ut labore et dolore magna aliqua. Quis ipsum suspendisse ultrices gravida. Risus commodo viverra maecenas accumsan lacus vel facilisis. Lorem ipsum dolor sit amet, consectetur adipiscing elit, sed do eiusmod tempor incididunt ut labore et dolore magna aliqua. Quis ipsum suspendisse ultrices gravida. Risus commodo viverra maecenas accumsan lacus vel facilisis.</blockquote>
  <cite>- Martin Keller</cite>
  <span class="slider-arrow next"><svg width="12" height="16" viewBox="0 0 12 16"><path d="M4 2l6 6-6 6" fill="none" stroke="#333" stroke-width="1.6"/></svg></span>
</section>

<footer class="site-footer">
  <div class="wordmark"><span class="mark"></span>BASALT GUARD</div>
  <div class="foot-col" style="left:519px">
    <h4>Company</h4>
    <a href="#">Home</a><a href="#">About Me</a><a href="#">Services</a><a href="#">Blogs</a><a href="#">Contact Us</a>
  </div>
  <div class="foot-col" style="left:700px">
    <h4>Resources</h4>
    <a href="#">Support</a><a href="#">Testimonials</a><a href="#">Sitemap</a><a href="#">Career</a><a href="#">Contact Us</a>
  </div>
  <div class="foot-col" style="left:919px">
    <h4>Contact Us</h4>
    <ul class="contact-list">
      <li><svg width="18" height="20" viewBox="0 0 18 20" fill="none" stroke="#1aa8ec" stroke-width="1.5"><path d="M9 19s7-7 7-11A7 7 0 0 0 2 8c0 4 7 11 7 11z"/><circle cx="9" cy="8" r="2.5"/></svg><span>110 w 90 Lorem sed sit<br>Location 0000 NX</span></li>
      <li><svg width="20" height="18" viewBox="0 0 20 18" fill="none" stroke="#1aa8ec" stroke-width="1.5"><path d="M4 1l4 4-2 3c1 2 3 4 5 5l3-2 4 4-3 2C9 17 2 10 1 4z"/></svg><span>(888) 888 8888</span></li>
      <li><svg width="22" height="16" viewBox="0 0 22 16" fill="none" stroke="#1aa8ec" stroke-width="1.5"><rect x="1" y="1" width="20" height="14"/><path d="M1 1l10 8 10-8"/></svg><span>info@basaltguard.com</span></li>
    </ul>
    <div class="socials" aria-label="Social media links"><span></span><span></span><span></span><span></span></div>
  </div>
</footer>
<div class="copyright">Copyright © 2021 Basaltguard. All Rights Reserved.</div>

</body>
</html>
```